Web Design for a Biotech Consulting Firm

We need a web site design for a new business based in Philadelphia called Verantel Dx. This is a consulting firm that will serve medical diagnostics industry, which is part of the life science/healthcare industry focusing on developing and marketing products that help in early detection, monitoring or management of diseases. Our consulting firm will help medical diagnostic companies to overcome key challenges in designing, evaluating and marketing new products.Our company name is Verantel Dx. Verantel is Latin word for "something" Dx represents diagnostics. The idea behind the name is that we help companies to transform the original, early product ideas ("nothing") into "something"; which is a product with full clinical utility that will help to improve health and well-being.The web site should use the visual feel of the logo (attached), be modern, simple and clean looking and represent creativity, innovation, scientific thinking and progress.
Updates

Wix Design is acceptable

Industry/Entity Type

Biotechnology

Coding

Coded - Design and coding required

Number of Pages Required

1 page

Font styles to use
Sans Serif

Requirements
Must have
• simple, clean look couple of pages
Should not have
• a lot of pages

```html
<!DOCTYPE html>
<html lang="en">
<head>
<meta charset="utf-8">
<title>Verantel Dx — Biotech Consulting</title>
<link href="https://fonts.googleapis.com/css2?family=Mulish:wght@300;400;600;700&display=swap" rel="stylesheet">
<style>
:root{
  --blue:#3a73c7;
  --blue-soft:#5b8fd8;
  --ink:#1d1d1f;
  --text:#4a4a4a;
  --muted:#7a7a7a;
  --line:#cfd9ea;
  --pale:#eef3fa;
  --white:#ffffff;
}
*{margin:0;padding:0;box-sizing:border-box}
html,body{width:1200px;height:3457px;overflow:hidden}
body{font-family:'Mulish',sans-serif;color:var(--text);background:var(--white);position:relative}
.abs{position:absolute}
.brand{display:flex;align-items:center;gap:8px;font-weight:600;color:var(--ink);font-size:17px}
.brand-square{width:10px;height:10px;background:var(--blue)}
.nav{left:530px;top:38px;display:flex;gap:42px;font-size:14px;color:#333}
.nav .active{font-weight:700;border:1px solid var(--blue);border-width:1px 0 0 1px;padding:2px 6px;margin:-3px -6px}
.phone{left:935px;top:30px;display:flex;gap:10px;align-items:center;font-size:12px;color:#555;line-height:1.3}
.phone-divider{left:915px;top:28px;width:1px;height:40px;background:#ddd}
.hero{left:0;top:100px;width:1200px;height:542px;background:linear-gradient(120deg,#2f3b45 0%,#5f7583 45%,#8aa1ad 70%,#3e9ba0 100%)}
.hero h1{position:absolute;left:143px;top:172px;color:#fff;font-weight:600;font-size:36px;line-height:46px;letter-spacing:.3px}
.hero h1 span{display:block}
.hero h1 .gap{margin-top:6px}
.dots{left:141px;top:591px;display:flex;gap:12px}
.dots i{width:13px;height:13px;border:1px solid #fff}
.dots i.on{background:#fff}
.intro-title{left:0;width:1200px;top:728px;text-align:center;font-size:28px;font-weight:600;color:var(--ink)}
.intro-sub{left:0;width:1200px;top:770px;text-align:center;font-size:28px;color:var(--blue-soft)}
.card{top:856px;height:206px;border:1.5px solid #777;background:#fff;text-align:center;padding-top:20px}
.card.feature{border-color:var(--blue)}
.card h3{font-size:18px;font-weight:500;color:var(--ink);margin-top:10px}
.card p{font-size:12px;color:#555;line-height:16px;margin:12px auto 0;width:170px}
.numeral{font-size:120px;font-weight:200;line-height:1;color:transparent;-webkit-text-stroke:1.5px #666}
.numeral.blue{-webkit-text-stroke-color:var(--blue)}
.btn{display:flex;align-items:center;justify-content:center;gap:8px;border:1.5px solid var(--blue);border-right:none;font-size:14px;color:#555;height:34px}
.btn svg{margin-right:-14px}
.about{left:0;top:1233px;width:1200px;height:438px;background:linear-gradient(100deg,#4f86d6 0%,#6fa0e4 40%,#4a80d2 100%);color:#fff;text-align:center}
.about h2{position:absolute;top:86px;width:100%;font-size:28px;font-weight:600}
.about .rule{position:absolute;left:564px;top:138px;width:72px;height:1px;background:rgba(255,255,255,.7)}
.about .lead{position:absolute;top:162px;width:100%;font-size:15px;line-height:24px}
.about .body{position:absolute;left:180px;width:840px;top:222px;font-size:13.5px;line-height:21px}
.about .btn{position:absolute;left:543px;top:311px;width:104px;border-color:#fff;color:#fff}
.photo-lab{left:0;top:1671px;width:648px;height:435px;background:linear-gradient(135deg,#d7e6f2 0%,#9fbfd9 50%,#e6eef5 100%)}
.asset h2{left:722px;top:1832px;font-size:28px;font-weight:600;color:var(--ink)}
.asset p{left:720px;top:1880px;width:360px;font-size:18px;line-height:29px;color:#444}
.blue-word{color:var(--blue-soft)}
.stats{left:0;top:2106px;width:1200px;height:221px;background:var(--pale)}
.stat{top:2180px;width:260px;text-align:center;margin-left:-130px}
.stat b{display:block;font-size:36px;font-weight:600;color:var(--blue)}
.stat span{display:block;font-size:15px;font-weight:600;color:#222;margin-top:2px}
.stat-div{top:2172px;height:82px;border-left:1px dashed #b9c7dc}
.news-photo{left:0;top:2327px;width:1200px;height:438px;background:linear-gradient(90deg,#f2f4f6 0%,#e9edf1 45%,#b7c3cb 65%,#e0e5ea 100%)}
.news h2{left:140px;top:2410px;font-size:28px;font-weight:700;color:var(--ink)}
.news-item{left:143px;width:350px;font-size:13.5px;line-height:21px;color:#333}
.news-meta{left:143px;width:340px;display:flex;justify-content:space-between;font-size:13px;color:#333}
.news-meta .more{font-weight:700;font-size:12px;display:flex;gap:8px;align-items:center}
.news-meta .date{display:flex;gap:10px;align-items:center}
.news-rule{left:140px;top:2576px;width:354px;border-top:1px dashed #9fb2cc}
.contact-title{left:0;width:1200px;top:2850px;text-align:center;font-size:28px;font-weight:600;color:var(--ink)}
.form-box{left:142px;top:2928px;width:600px;height:327px;background:#f4f6f9}
.info-box{left:740px;top:2928px;width:319px;height:327px;background:#e9eff8}
.field{width:235px;border-bottom:1px dashed #9fb2cc;font-size:12px;color:#555;height:28px}
.info-row{left:776px;display:flex;gap:18px;align-items:flex-start;font-size:13.5px;line-height:21px;color:#333}
.info-icon{width:38px;height:40px;border:1.5px solid var(--blue);background:#fff;display:flex;align-items:center;justify-content:center;flex-shrink:0}
.footer-links{left:352px;top:3354px;display:flex;gap:14px;align-items:center;font-size:13px;color:#333}
.footer-links i{width:4px;height:4px;border-radius:50%;background:#aab;display:block;margin:0 10px}
.copy{left:778px;top:3355px;font-size:12.5px;color:#333}
.bottom-bar{left:0;top:3454px;width:1200px;height:3px;background:var(--blue)}
</style>
</head>
<body>

<header>
  <div class="abs brand" style="left:142px;top:36px"><span class="brand-square"></span>Verantel Dx</div>
  <nav class="abs nav"><span class="active">Home</span><span>About Us</span><span>Services</span><span>Contact Us</span></nav>
  <div class="abs phone-divider"></div>
  <div class="abs phone">
    <svg width="24" height="24" viewBox="0 0 24 24"><circle cx="12" cy="12" r="11" fill="none" stroke="#3a73c7" stroke-width="1.5"/><path d="M8 7c1 0 2 2 2 3s-1 1-1 2 2 3 3 3 1-1 2-1 3 1 3 2-2 2-3 2c-4 0-8-4-8-8 0-1 1-3 2-3z" fill="none" stroke="#3a73c7" stroke-width="1.3"/></svg>
    <div>PHONE<br>123-456-7890</div>
  </div>
</header>

<section class="abs hero" role="img" aria-label="Photo of a gloved hand pipetting into a tray of sample tubes over a petri dish">
  <h1><span>We Are</span><span>A Biotech Consulting Firm</span><span class="gap">Serving The Medical</span><span>Diagnostics Industry</span></h1>
</section>
<div class="abs dots"><i class="on"></i><i></i><i></i><i></i></div>

<section class="services">
  <h2 class="abs intro-title">Our Consulting Firm Will Help Medical Diagnostic Companies</h2>
  <p class="abs intro-sub">To Overcome Key Challenges In</p>

  <div class="abs numeral" style="left:140px;top:880px">1</div>
  <div class="abs card" style="left:198px;width:224px">
    <svg width="60" height="56" viewBox="0 0 60 56" fill="none" stroke="#555" stroke-width="1.5"><circle cx="20" cy="14" r="7"/><circle cx="40" cy="14" r="7"/><circle cx="12" cy="32" r="6"/><circle cx="30" cy="44" r="7"/><circle cx="46" cy="34" r="6"/><path d="M20 21l-6 6M27 14h6M40 21l5 7M18 36l6 4M37 43l5-4"/></svg>
    <h3>Designing</h3>
    <p>Lorem ipsum dolor sit amet, consectetuer adipiscing sed diam nonummy</p>
  </div>

  <div class="abs numeral blue" style="left:456px;top:880px">2</div>
  <div class="abs card feature" style="left:525px;width:217px">
    <svg width="60" height="56" viewBox="0 0 60 56" fill="none" stroke="#3a73c7" stroke-width="1.5"><rect x="6" y="16" width="48" height="30"/><path d="M2 50h56"/><circle cx="30" cy="14" r="10" fill="#fff"/><path d="M30 6v8h7"/><path d="M14 40v-8M22 40v-12M38 40v-10M46 40v-6"/></svg>
    <h3>Market Analysis</h3>
    <p>Lorem ipsum dolor sit amet, consectetuer adipiscing sed diam nonummy</p>
  </div>

  <div class="abs numeral" style="left:778px;top:880px">3</div>
  <div class="abs card" style="left:847px;width:211px">
    <svg width="70" height="56" viewBox="0 0 70 56" fill="none" stroke="#555" stroke-width="1.5"><rect x="4" y="8" width="34" height="26"/><path d="M14 44h14M21 34v10"/><path d="M38 22l12-8v22l-12-8z"/><path d="M56 16l5-3M56 25h6M56 34l5 3"/><circle cx="16" cy="20" r="5"/></svg>
    <h3>Product Launch</h3>
    <p>Lorem ipsum dolor sit amet, consectetuer adipiscing sed diam nonummy</p>
  </div>

  <div class="abs btn" style="left:547px;top:1105px;width:98px">Get Started
    <svg width="16" height="10" viewBox="0 0 16 10"><path d="M0 5h14M10 1l4 4-4 4" fill="none" stroke="#3a73c7"/></svg></div>
</section>

<section class="abs about">
  <h2>About Verantel Dx</h2>
  <div class="rule"></div>
  <p class="lead">Verantel Dx This Is A Consulting Firm That Will Serve Medical Diagnostics Industry,<br>Which Is Part of The Life Science/healthcare Industry</p>
  <p class="body">Lorem ipsum dolor sit amet, consectetuer adipiscing elit, sed diam nonummy nibh euismod tincidunt ut laoreet dolore magna aliquam erat volutpat. Ut wisi enim ad minim veniam, quis nostrud exerci tation ullamcorper suscipit lobortis nisl ut aliquip ea commodo consequat. Duis autem vel eum iriure or sit amet, consectetuer adipiscing elit</p>
  <div class="btn">Read More <svg width="16" height="10" viewBox="0 0 16 10"><path d="M0 5h14M10 1l4 4-4 4" fill="none" stroke="#fff"/></svg></div>
</section>

<section class="asset">
  <div class="abs photo-lab" role="img" aria-label="Photo of a scientist in a lab coat working with a flask beside a microscope"></div>
  <h2 class="abs">Asset <span class="blue-word">Partnering</span></h2>
  <p class="abs">Learn about our current partnering opportunities and submit your assets.</p>
  <div class="abs btn" style="left:720px;top:1957px;width:96px">Learn More <svg width="16" height="10" viewBox="0 0 16 10"><path d="M0 5h14M10 1l4 4-4 4" fill="none" stroke="#3a73c7"/></svg></div>
</section>

<section>
  <div class="abs stats"></div>
  <div class="abs stat" style="left:232px"><b>100</b><span>PROFESSIONAL STAFF</span></div>
  <div class="abs stat-div" style="left:381px"></div>
  <div class="abs stat" style="left:470px"><b>50</b><span>ROOMS</span></div>
  <div class="abs stat-div" style="left:560px"></div>
  <div class="abs stat" style="left:686px"><b>10</b><span>STARS COMFORT</span></div>
  <div class="abs stat-div" style="left:813px"></div>
  <div class="abs stat" style="left:964px"><b>25</b><span>YEARS OF EXPERIENCE</span></div>
</section>

<section class="news">
  <div class="abs news-photo" role="img" aria-label="Photo of two researchers at a microscope in a bright laboratory"></div>
  <h2 class="abs">Latest <span class="blue-word">News</span></h2>
  <p class="abs news-item" style="top:2470px">Lorem Quis nostrud exerci tation ullamcorper suscipit lobortis nisl ut aliquip ex ea commo</p>
  <div class="abs news-meta" style="top:2525px"><span class="date"><svg width="14" height="14" viewBox="0 0 14 14"><rect x="1" y="2" width="12" height="11" fill="none" stroke="#3a73c7"/><path d="M1 5h12M4 0v3M10 0v3" stroke="#3a73c7"/></svg>June 17, 2019</span><span class="more">READ MORE <svg width="16" height="10" viewBox="0 0 16 10"><path d="M0 5h14M10 1l4 4-4 4" fill="none" stroke="#3a73c7"/></svg></span></div>
  <div class="abs news-rule"></div>
  <p class="abs news-item" style="top:2604px">Lorem Quis nostrud exerci tation ullamcorper suscipit lobortis nisl ut aliquip ex ea commo</p>
  <div class="abs news-meta" style="top:2661px"><span class="date"><svg width="14" height="14" viewBox="0 0 14 14"><rect x="1" y="2" width="12" height="11" fill="none" stroke="#3a73c7"/><path d="M1 5h12M4 0v3M10 0v3" stroke="#3a73c7"/></svg>June 17, 2019</span><span class="more">READ MORE <svg width="16" height="10" viewBox="0 0 16 10"><path d="M0 5h14M10 1l4 4-4 4" fill="none" stroke="#3a73c7"/></svg></span></div>
</section>

<section class="contact">
  <h2 class="abs contact-title">CONTACT <span class="blue-word">US</span></h2>
  <div class="abs form-box"></div>
  <div class="abs field" style="left:178px;top:2990px">Name</div>
  <div class="abs field" style="left:442px;top:2990px">Phone</div>
  <div class="abs field" style="left:178px;top:3044px">Email</div>
  <div class="abs field" style="left:442px;top:3044px">Company Name</div>
  <div class="abs field" style="left:178px;top:3098px;width:499px;height:42px">Message</div>
  <div class="abs btn" style="left:178px;top:3165px;width:98px">SUBMIT <svg width="16" height="10" viewBox="0 0 16 10"><path d="M0 5h14M10 1l4 4-4 4" fill="none" stroke="#3a73c7"/></svg></div>

  <div class="abs info-box"></div>
  <div class="abs info-row" style="top:2988px"><span class="info-icon"><svg width="14" height="18" viewBox="0 0 14 18"><path d="M7 17s6-6 6-10A6 6 0 0 0 1 7c0 4 6 10 6 10z" fill="none" stroke="#3a73c7" stroke-width="1.5"/><circle cx="7" cy="7" r="2" fill="#3a73c7"/></svg></span><span>Lorem Quis nostrud exercitionl<br>ullamcorper suscipit - 123 456</span></div>
  <div class="abs info-row" style="top:3065px"><span class="info-icon"><svg width="16" height="16" viewBox="0 0 16 16"><path d="M4 1c1 0 2 3 2 4s-1 1-1 2 3 4 4 4 1-1 2-1 4 1 4 2-2 3-3 3C6 15 1 10 1 4c0-1 2-3 3-3z" fill="#3a73c7"/></svg></span><span>CALL US :<br>123-456-7890</span></div>
  <div class="abs info-row" style="top:3143px"><span class="info-icon"><svg width="16" height="16" viewBox="0 0 16 16"><path d="M15 1L1 7l5 2 2 6 7-14z" fill="#3a73c7"/></svg></span><span>EMAIL US:<br>info@verantel-dx.com</span></div>
</section>

<footer>
  <div class="abs brand" style="left:178px;top:3354px"><span class="brand-square"></span>Verantel Dx</div>
  <nav class="abs footer-links"><span>Home</span><i></i><span>About Us</span><i></i><span>Services</span><i></i><span>Contact Us</span></nav>
  <p class="abs copy">Copyright © 2019 Verantel Dx . All Rights Reserved.</p>
  <div class="abs bottom-bar"></div>
</footer>

</body>
</html>
```